Belmont Ridge Business Card Design Project

We have recently rebranded and would like to design new business cards that incorporate the corporate logo - double sided cards with corporate logo on one side and contact details on the other

Target Market(s)

Sophisticated and high net worth investors and finance industry professionals

Industry/Entity Type

Funds Management

Contact Information for Business Card

The card should prominently feature the company name and logo. Other details will be standard contact details for each staff member - name, address, phone, email, website

Colors
0054AA
0677BA
7BADD7
CADEEF
E8F1F8

Requirements
Must have
• Double-sided design with one side prominently featuring the corporate logo and the other side with all standard contact details

```html
<!DOCTYPE html>
<html lang="en">
<head>
<meta charset="utf-8">
<title>Belmont Ridge — Business Card</title>
<link href="https://fonts.googleapis.com/css2?family=Cinzel:wght@700&family=Montserrat:wght@400&display=swap" rel="stylesheet">
<style>
  :root {
    --backdrop: #d4d7d8;
    --paper: #f7f7f6;
    --navy: #17406f;
    --navy-deep: #143a66;
    --ink: #3d3f44;
    --rule: #2f5a8c;
    --white: #ffffff;
  }
  * { box-sizing: border-box; margin: 0; padding: 0; }
  html, body {
    width: 1200px; height: 905px; overflow: hidden;
    background: var(--backdrop);
  }
  .canvas {
    position: relative; width: 1200px; height: 905px;
    display: flex; flex-direction: column; align-items: center;
    justify-content: center; gap: 35px;
  }
  .card {
    position: relative; width: 700px; height: 400px;
    box-shadow: 0 10px 28px rgba(0,0,0,0.18);
  }
  .card-front { background: var(--paper); }
  .card-back {
    background: var(--navy-deep);
    display: flex; align-items: center; justify-content: center;
  }
  .wordmark {
    display: flex; align-items: center; gap: 14px;
    font-family: "Cinzel", serif; font-weight: 700;
    letter-spacing: 1px; white-space: nowrap;
  }
  .wordmark-dot { width: 22px; height: 22px; border-radius: 50%; }
  .card-front .wordmark {
    position: absolute; right: 50px; top: 78px;
    font-size: 36px; color: var(--navy);
  }
  .card-front .wordmark-dot { background: var(--navy); }
  .card-back .wordmark { font-size: 54px; color: var(--white); }
  .card-back .wordmark-dot { width: 30px; height: 30px; background: var(--white); }

  .holder { position: absolute; left: 58px; top: 60px; }
  .holder-name {
    font-family: "Cinzel", serif; font-weight: 700;
    font-size: 28px; color: var(--navy); letter-spacing: 0.5px;
  }
  .holder-title {
    font-family: "Montserrat", sans-serif; font-size: 17px;
    color: var(--ink); margin-top: 2px;
  }
  .rule-horizontal {
    position: absolute; left: 55px; right: 55px; top: 148px;
    height: 1.5px; background: var(--rule);
  }
  .rule-vertical {
    position: absolute; left: 330px; top: 190px;
    width: 1.5px; height: 120px; background: var(--rule);
  }
  .contact-list {
    position: absolute; left: 58px; top: 180px; list-style: none;
    font-family: "Montserrat", sans-serif; font-size: 17px; color: var(--ink);
  }
  .contact-list li { display: flex; align-items: center; gap: 12px; height: 36px; }
  .contact-list svg { width: 17px; height: 17px; fill: var(--navy); flex: none; }
  .address {
    position: absolute; left: 362px; top: 206px;
    font-family: "Montserrat", sans-serif; font-size: 18px;
    line-height: 34px; color: var(--ink); font-style: normal;
  }
</style>
</head>
<body>
<main class="canvas">
  <section class="card card-front" aria-label="Card front with contact details">
    <div class="holder">
      <p class="holder-name">Daniel Harper</p>
      <p class="holder-title">CEO/Founder</p>
    </div>
    <div class="wordmark"><span class="wordmark-dot"></span>Belmont Ridge</div>
    <div class="rule-horizontal"></div>
    <ul class="contact-list">
      <li>
        <svg viewBox="0 0 24 24" aria-hidden="true"><path d="M6.6 10.8a15.1 15.1 0 0 0 6.6 6.6l2.2-2.2a1 1 0 0 1 1-.25 11.4 11.4 0 0 0 3.6.57 1 1 0 0 1 1 1V20a1 1 0 0 1-1 1A17 17 0 0 1 3 4a1 1 0 0 1 1-1h3.5a1 1 0 0 1 1 1c0 1.25.2 2.45.57 3.57a1 1 0 0 1-.25 1z"/></svg>
        (555) 418-2097
      </li>
      <li>
        <svg viewBox="0 0 24 24" aria-hidden="true"><path d="M2 5h20v14H2z M2 5l10 8 10-8" fill="none" stroke="#17406f" stroke-width="2"/><path d="M2 5h20l-10 8z"/></svg>
        info@belmontridge.com
      </li>
      <li>
        <svg viewBox="0 0 24 24" aria-hidden="true"><circle cx="12" cy="12" r="9.5" fill="none" stroke="#17406f" stroke-width="2"/><path d="M2.5 12h19M12 2.5v19M12 2.5c-5 5-5 14 0 19M12 2.5c5 5 5 14 0 19" fill="none" stroke="#17406f" stroke-width="1.5"/></svg>
        www.belmontridge.com
      </li>
    </ul>
    <div class="rule-vertical"></div>
    <address class="address">Po Box 3190 Harbour Lane<br>Westland AB 7261</address>
  </section>

  <section class="card card-back" aria-label="Card back with company name">
    <div class="wordmark"><span class="wordmark-dot"></span>Belmont Ridge</div>
  </section>
</main>
</body>
</html>
```